need corporate, modern business card created for Consulting Company

I need a slick business card using elements from my website, as well as, integrating my pixelforge-created logo (see files).

The business card needs to be:
1. Corporate and modern
2. Clean and professional

I've included a PSD with the logo/icon that you can use to create it. Feel free to try a metallic finish on the logo, make it bigger/small, underlay it. Whatever you need to do to make my card stand out.

Try a black background, or white background or gray.

The idea is for my card to be memorable as well as professional and corporate.

Target Market(s)

Corporate business in the US and Canada.

Industry/Entity Type

Business

Contact Information for Business Card

Commerce Advancing Methods
Martin Coles, Senior Partner
office: 1 877 555 0143
mobile: 1 519 555 0172
website: http://www.brightvale.example

Requirements
Must have
• Card-related information
• corporate, yet modern
• clean and professional
• incorporate the icon only
• must have an editable form when complete!
Nice to have
• metallic icon might be cool
• try it with white or black

```html
<!DOCTYPE html>
<html lang="en">
<head>
<meta charset="utf-8">
<title>Brightvale Business Card</title>
<link href="https://fonts.googleapis.com/css2?family=Montserrat:wght@500;600;700&display=swap" rel="stylesheet">
<style>
  :root {
    --stage: #e9e7e3;
    --brand-blue: #3d8fd4;
    --brand-blue-light: #4ba3df;
    --brand-blue-deep: #2a72b8;
    --ink: #2b2b2b;
    --ink-soft: #4a4a4a;
    --paper: #ffffff;
    --paper-shade: #e6e6e6;
  }
  * { box-sizing: border-box; margin: 0; padding: 0; }
  html, body { width: 1200px; height: 885px; overflow: hidden; }
  body {
    background: var(--stage);
    font-family: "Montserrat", sans-serif;
    position: relative;
  }

  /* Front of card */
  .card-front {
    position: absolute;
    left: 50px;
    top: 265px;
    width: 620px;
    height: 354px;
    border-radius: 4px;
    background: radial-gradient(ellipse at 55% 40%, var(--brand-blue-light) 0%, var(--brand-blue) 55%, var(--brand-blue-deep) 100%);
    box-shadow: 0 10px 24px rgba(0,0,0,0.18);
    display: flex;
    align-items: center;
    justify-content: center;
  }
  .front-wordmark {
    display: flex;
    align-items: center;
    gap: 18px;
  }
  .front-wordmark .mark-square {
    width: 34px;
    height: 34px;
    background: var(--paper);
    border-radius: 4px;
  }
  .front-wordmark .brand-name {
    color: var(--paper);
    font-weight: 700;
    font-size: 72px;
    letter-spacing: -1px;
  }

  /* Back of card */
  .card-back {
    position: absolute;
    left: 790px;
    top: 132px;
    width: 354px;
    height: 620px;
    border-radius: 4px;
    background: linear-gradient(160deg, var(--paper) 0%, var(--paper) 55%, var(--paper-shade) 100%);
    box-shadow: 0 10px 24px rgba(0,0,0,0.18);
    overflow: hidden;
    display: flex;
    flex-direction: column;
    align-items: center;
  }
  .back-logo {
    margin-top: 90px;
    display: flex;
    flex-direction: column;
    align-items: center;
  }
  .back-logo .mark-square {
    width: 30px;
    height: 30px;
    background: var(--brand-blue);
    border-radius: 4px;
    margin-bottom: 14px;
  }
  .back-logo .brand-name {
    color: var(--brand-blue);
    font-weight: 700;
    font-size: 50px;
    letter-spacing: -1px;
    line-height: 1;
  }
  .tagline {
    margin-top: 8px;
    color: var(--ink-soft);
    font-weight: 600;
    font-size: 13px;
  }
  .person {
    margin-top: 44px;
    text-align: center;
  }
  .person-name {
    color: var(--ink);
    font-weight: 700;
    font-size: 30px;
  }
  .person-title {
    color: var(--brand-blue);
    font-weight: 500;
    font-size: 20px;
    margin-top: 2px;
  }
  .contacts {
    margin-top: 30px;
    list-style: none;
    color: var(--ink);
    font-weight: 600;
    font-size: 19px;
    line-height: 1.4;
  }
  .contacts li { display: flex; align-items: center; gap: 8px; }
  .contacts svg { width: 18px; height: 18px; flex: none; }
  .address {
    margin-top: 24px;
    text-align: center;
    color: var(--ink);
    font-weight: 600;
    font-size: 14px;
    line-height: 1.5;
  }
  .web-band {
    position: absolute;
    left: 0;
    right: 0;
    bottom: 0;
    height: 62px;
    background: var(--brand-blue);
    border-top: 3px solid var(--paper);
    box-shadow: 0 -2px 0 var(--brand-blue);
    display: flex;
    align-items: center;
    justify-content: center;
    color: var(--paper);
    font-weight: 500;
    font-size: 21px;
    letter-spacing: 0.5px;
  }
</style>
</head>
<body>

  <section class="card-front" aria-label="Card front">
    <div class="front-wordmark">
      <span class="mark-square"></span>
      <span class="brand-name">brightvale</span>
    </div>
  </section>

  <section class="card-back" aria-label="Card back">
    <div class="back-logo">
      <span class="mark-square"></span>
      <span class="brand-name">brightvale</span>
      <span class="tagline">Commerce Advancing Methods</span>
    </div>

    <div class="person">
      <div class="person-name">Martin Coles</div>
      <div class="person-title">Senior Partner</div>
    </div>

    <ul class="contacts">
      <li>
        <svg viewBox="0 0 18 18" aria-hidden="true"><rect width="18" height="18" rx="3" fill="#3d8fd4"/><path d="M5 4.5c.6-.6 1.3-.5 1.7.1l1 1.5c.3.5.2 1-.2 1.4l-.6.5c.5 1.1 1.4 2 2.5 2.5l.5-.6c.4-.4.9-.5 1.4-.2l1.5 1c.6.4.7 1.1.1 1.7l-.6.6c-.8.8-3.2.3-5.3-1.8S3.6 5.9 4.4 5.1z" fill="#fff"/></svg>
        1 877 555 0143
      </li>
      <li>
        <svg viewBox="0 0 18 18" aria-hidden="true"><rect width="18" height="18" rx="3" fill="#3d8fd4"/><rect x="6" y="3.5" width="6" height="4" fill="#fff"/><rect x="3.5" y="7.5" width="11" height="5" rx="1" fill="#fff"/><rect x="6" y="11" width="6" height="3.5" fill="#fff" stroke="#3d8fd4" stroke-width=".8"/></svg>
        1 519 555 0172
      </li>
      <li>info@brightvale.example</li>
    </ul>

    <p class="address">14 Elm Crescent West, Suite 1208,<br>Lakeview, Ontario, L0K 9Z9</p>

    <div class="web-band">www.brightvale.example</div>
  </section>

</body>
</html>
```